Looking for a cool & simple business-card-design for digital agency

Hi!

We are a web agency that offers Reputation Management, Vextor & Seo Services and software development. We like cool things, we like innovative styles.

We have uploaded our logo.

Project Deadline Extended Reason: Client does not want any designs with the colorful logo. Please send us submissions ONLY with the blac and white logo. What the client would like to see:1) Back of the card: is a silver logo on a black background2) front of the card with all the data, please use white background and black logo thank you Added Friday, May 8, 2015

Industry/Entity Type

Software

```html
<!DOCTYPE html>
<html lang="en">
<head>
<meta charset="utf-8">
<title>NetPerk Stationery</title>
<link href="https://fonts.googleapis.com/css2?family=Open+Sans:wght@400;600;700&display=swap" rel="stylesheet">
<style>
  :root {
    --canvas: #ebebeb;
    --paper: #ffffff;
    --ink: #111111;
    --ink-soft: #3a3a3a;
    --grey-band: #5a5a5a;
    --grey-light: #d6d6d6;
    --rule: #c9c9c9;
    --silver: #d4d4d4;
    --card-black: #1c1c1c;
    --text-on-dark: #e6e6e6;
    --shadow: 0 4px 10px rgba(0,0,0,0.28);
  }
  * { margin: 0; padding: 0; box-sizing: border-box; }
  html, body { width: 1200px; height: 934px; overflow: hidden; }
  body {
    background: var(--canvas);
    font-family: "Open Sans", Arial, sans-serif;
    position: relative;
    color: var(--ink);
  }
  .sheet { position: absolute; background: var(--paper); box-shadow: var(--shadow); overflow: hidden; }
  .sheet svg.band { position: absolute; left: 0; bottom: 0; }

  .wordmark { position: absolute; display: flex; align-items: center; gap: 7px; }
  .wordmark-square { width: 16px; height: 16px; background: var(--ink); }
  .wordmark-text { display: flex; flex-direction: column; line-height: 1; }
  .wordmark-name { font-weight: 700; font-size: 18px; color: var(--ink); letter-spacing: 0.2px; }
  .wordmark-tag { font-size: 6.5px; letter-spacing: 2.4px; color: var(--ink-soft); margin-top: 2px; }

  .contact-list { position: absolute; list-style: none; font-size: 6px; line-height: 9px; text-align: right; }
  .contact-list li { display: flex; justify-content: flex-end; align-items: center; gap: 6px; }
  .contact-list .dot { width: 4px; height: 4px; border-radius: 50%; background: currentColor; display: inline-block; }

  /* Letterhead */
  .letterhead { left: 69px; top: 83px; width: 469px; height: 664px; }
  .letterhead .wordmark { left: 28px; top: 40px; }
  .letterhead .contact-list { right: 30px; top: 42px; color: var(--ink-soft); }
  .letterhead .footer-address { position: absolute; right: 32px; bottom: 26px; font-size: 6px; color: var(--text-on-dark); }

  /* Envelope front */
  .envelope-front { left: 564px; top: 83px; width: 567px; height: 257px; }
  .envelope-front .wordmark { left: 24px; top: 30px; }
  .envelope-front .return-address { position: absolute; left: 23px; top: 196px; font-size: 6px; color: var(--ink-soft); }
  .envelope-front .contact-list { right: 28px; top: 208px; color: var(--text-on-dark); }

  /* Envelope back */
  .envelope-back { left: 564px; top: 365px; width: 567px; height: 256px; }
  .envelope-back .flap { position: absolute; left: 0; top: 0; }
  .envelope-back .flap-url {
    position: absolute; left: 0; right: 0; top: 41px; text-align: center;
    font-size: 9px; letter-spacing: 2.6px; color: var(--text-on-dark);
  }

  /* Business cards */
  .card { position: absolute; width: 123px; height: 205px; box-shadow: var(--shadow); overflow: hidden; }

  .card-back { left: 564px; top: 646px; background: var(--card-black); color: var(--text-on-dark); }
  .card-back .silver-edge { position: absolute; left: 0; right: 0; height: 9px; background: linear-gradient(180deg, #9a9a9a, #f2f2f2 50%, #a8a8a8); }
  .card-back .silver-edge.top { top: 0; }
  .card-back .silver-edge.bottom { bottom: 0; }
  .card-back .card-name { position: absolute; left: 0; right: 0; top: 82px; text-align: center; font-weight: 700; font-size: 19px; color: var(--silver); }
  .card-back .card-tag { position: absolute; left: 0; right: 0; top: 108px; text-align: center; font-size: 6px; letter-spacing: 2px; color: var(--silver); }

  .card-front { left: 725px; top: 646px; background: var(--paper); color: var(--ink); }
  .card-front .card-name { position: absolute; left: 0; right: 0; top: 32px; text-align: center; font-weight: 700; font-size: 20px; color: var(--ink); }
  .card-front .divider { position: absolute; left: 14px; right: 14px; top: 100px; height: 1px; background: var(--rule); }
  .card-front .person { position: absolute; left: 0; right: 0; top: 104px; text-align: center; font-weight: 700; font-size: 7.5px; color: var(--ink); }
  .card-front .role { position: absolute; left: 0; right: 0; top: 116px; text-align: center; font-size: 4.5px; color: var(--ink-soft); }
  .card-front .divider.lower { top: 126px; }
  .card-front .card-contacts { position: absolute; left: 0; right: 0; top: 160px; list-style: none; font-size: 5px; line-height: 8px; text-align: center; color: var(--ink-soft); }
  .card-front .card-contacts .dot { width: 3px; height: 3px; border-radius: 50%; background: currentColor; display: inline-block; margin: 0 3px; vertical-align: middle; }
</style>
</head>
<body>

  <section class="sheet letterhead">
    <div class="wordmark">
      <span class="wordmark-square"></span>
      <div class="wordmark-text">
        <span class="wordmark-name">NetPerk</span>
        <span class="wordmark-tag">DIGITALE STRATEGIEN</span>
      </div>
    </div>
    <ul class="contact-list">
      <li>00.00.00.0000 <span class="dot"></span></li>
      <li>yourname@yourwebsite.com <span class="dot"></span></li>
      <li>www.yourwebsite.com <span class="dot"></span></li>
    </ul>
    <svg class="band" width="469" height="70" viewBox="0 0 469 70">
      <path d="M60 70 C140 28 260 12 469 10 L469 20 C280 20 160 34 76 70 Z" fill="var(--grey-light)"/>
      <path d="M95 70 C170 38 280 26 469 24 L469 70 Z" fill="var(--ink)"/>
    </svg>
    <p class="footer-address">Your Commercial or office address, pin code</p>
  </section>

  <section class="sheet envelope-front">
    <div class="wordmark">
      <span class="wordmark-square"></span>
      <div class="wordmark-text">
        <span class="wordmark-name">NetPerk</span>
        <span class="wordmark-tag">DIGITALE STRATEGIEN</span>
      </div>
    </div>
    <p class="return-address">Your Commercial or office address</p>
    <svg class="band" width="567" height="100" viewBox="0 0 567 100">
      <path d="M0 60 C80 60 180 95 300 82 C400 70 470 22 567 14 L567 20 C470 28 400 78 300 90 C180 104 80 70 0 68 Z" fill="var(--grey-band)"/>
      <path d="M0 76 C90 76 190 108 310 92 C410 78 480 34 567 26 L567 100 L0 100 Z" fill="var(--ink)"/>
    </svg>
    <ul class="contact-list">
      <li>00.00.00.0000 <span class="dot"></span></li>
      <li>yourname@yourwebsite.com <span class="dot"></span></li>
      <li>www.yourwebsite.com <span class="dot"></span></li>
    </ul>
  </section>

  <section class="sheet envelope-back">
    <svg class="flap" width="567" height="92" viewBox="0 0 567 92">
      <path d="M0 0 L567 0 L522 92 L45 92 Z" fill="var(--ink)"/>
    </svg>
    <p class="flap-url">www.netperk.com</p>
  </section>

  <section class="card card-back">
    <div class="silver-edge top"></div>
    <p class="card-name">NetPerk</p>
    <p class="card-tag">DIGITALE STRATEGIEN</p>
    <div class="silver-edge bottom"></div>
  </section>

  <section class="card card-front">
    <p class="card-name">NetPerk</p>
    <div class="divider"></div>
    <p class="person">Your Long Name</p>
    <p class="role">Managing Director</p>
    <div class="divider lower"></div>
    <ul class="card-contacts">
      <li><span class="dot"></span>Your Commercial or office address</li>
      <li><span class="dot"></span>00.00.00.0000<span class="dot"></span>00.00.00.0000</li>
      <li><span class="dot"></span>yourname@yourwebsite.com</li>
      <li><span class="dot"></span>www.yourwebsite.com</li>
    </ul>
  </section>

</body>
</html>
```